Velk Partners Building Business Cards

We need a business card that reflects our business as "Solar Experts" in San Diego. Browse our website www.velkpartners.example our License needs to be displayed as "CSLB# 3867140" our phone number is (619) 555-0187

Save thousands on your electric bills and increase the value of your home while helping to protect the environment. Our solar installation experts will help you design the system that's right for you, using only the highest quality equipment that will look great and give you ideal performance. Our goal is to make you energy independent, and get your electric bill to 0.

Paul Osterby
(619) 555-0187
paul@velkpartners.example

Target Market(s)

Home owners in san diego looking for solar

Industry/Entity Type

Solar Energy

Contact Information for Business Card

Paul Osterby
(619) 555-0187
paul@velkpartners.example

Font styles to use
Other font styles liked:
• Use our logo font

Requirements
Must have
• License needs to be displayed as "CSLB# 3867140" our phone number is (619) 555-0187
Nice to have
• Real images of rooftop home solar in san diego
Should not have
• our business address

```html
<!DOCTYPE html>
<html lang="en">
<head>
<meta charset="utf-8">
<title>Velk Partners Building — Business Card</title>
<link rel="stylesheet" href="https://fonts.googleapis.com/css2?family=Open+Sans:ital,wght@0,400;0,600;0,700;1,400&display=swap">
<style>
  :root {
    --navy: #1b3f78;
    --sun: #f6ab00;
    --ink: #555a60;
    --paper: #ffffff;
    --backdrop: #4b4b4b;
    --rule: #4a5e80;
  }
  * { box-sizing: border-box; margin: 0; padding: 0; }
  html, body { width: 1105px; height: 1200px; overflow: hidden; }
  body {
    background: var(--backdrop);
    font-family: "Open Sans", Arial, sans-serif;
    position: relative;
  }
  .card {
    position: absolute;
    left: 193px;
    width: 718px;
    height: 410px;
    border-radius: 19px;
    overflow: hidden;
  }
  .card--front { top: 167px; background: var(--paper); }
  .card--back { top: 623px; background: var(--navy); }

  .front__waves { position: absolute; inset: 0; width: 718px; height: 410px; }

  .wordmark {
    position: absolute;
    left: 46px;
    top: 54px;
    font-size: 29px;
    font-weight: 700;
    color: var(--navy);
    letter-spacing: -0.3px;
    white-space: nowrap;
  }

  .holder {
    position: absolute;
    right: 44px;
    top: 200px;
    text-align: right;
  }
  .holder__name { font-size: 24px; font-weight: 600; color: var(--navy); line-height: 1.15; }
  .holder__title { font-size: 18px; color: var(--sun); line-height: 1.3; }

  .divider {
    position: absolute;
    left: 50px;
    right: 44px;
    top: 270px;
    height: 1px;
    background: var(--rule);
  }

  .contact {
    position: absolute;
    left: 50px;
    top: 286px;
    list-style: none;
    font-size: 18px;
    color: var(--ink);
    line-height: 28px;
  }
  .contact__item { display: flex; align-items: center; gap: 10px; }
  .contact__icon { width: 16px; height: 16px; fill: var(--navy); flex: none; }

  .credentials {
    position: absolute;
    right: 44px;
    top: 286px;
    text-align: right;
    font-size: 18px;
    line-height: 28px;
  }
  .credentials__license { color: var(--ink); }
  .credentials__web { color: var(--navy); font-weight: 700; }

  .back__brand {
    position: absolute;
    left: 0; right: 0;
    top: 160px;
    display: flex;
    justify-content: center;
    align-items: center;
    gap: 16px;
  }
  .back__dot { width: 40px; height: 40px; border-radius: 50%; background: var(--sun); }
  .back__name { font-size: 34px; font-weight: 700; color: var(--paper); white-space: nowrap; }
  .back__web {
    position: absolute;
    left: 0; right: 0;
    top: 336px;
    text-align: center;
    font-size: 18px;
    font-style: italic;
    letter-spacing: 4px;
    color: var(--paper);
  }
</style>
</head>
<body>
  <section class="card card--front" aria-label="Business card front">
    <svg class="front__waves" viewBox="0 0 718 410" aria-hidden="true">
      <path d="M0,334 C140,372 300,378 718,360 L718,366 C420,378 200,384 0,372 Z" fill="var(--sun)"/>
      <path d="M0,374 C210,388 460,356 718,384 L718,410 L0,410 Z" fill="var(--navy)"/>
    </svg>

    <div class="wordmark">Velk Partners Building</div>

    <div class="holder">
      <div class="holder__name">Paul Osterby</div>
      <div class="holder__title">CEO/Founder</div>
    </div>

    <div class="divider"></div>

    <ul class="contact">
      <li class="contact__item">
        <svg class="contact__icon" viewBox="0 0 24 24" aria-hidden="true"><path d="M6.6 10.8a15.1 15.1 0 0 0 6.6 6.6l2.2-2.2a1 1 0 0 1 1-.25 11.4 11.4 0 0 0 3.6.57 1 1 0 0 1 1 1V20a1 1 0 0 1-1 1A17 17 0 0 1 3 4a1 1 0 0 1 1-1h3.5a1 1 0 0 1 1 1c0 1.25.2 2.45.57 3.57a1 1 0 0 1-.25 1Z"/></svg>
        <span>(619) 555-0187</span>
      </li>
      <li class="contact__item">
        <svg class="contact__icon" viewBox="0 0 24 24" aria-hidden="true"><path d="M2 5h20v14H2Z M3.5 6.5 12 13l8.5-6.5" fill="var(--navy)" stroke="#fff" stroke-width="1.4"/></svg>
        <span>paul@velkpartners.example</span>
      </li>
    </ul>

    <div class="credentials">
      <div class="credentials__license">CSLB# 3867140</div>
      <div class="credentials__web">www.velkpartners.example</div>
    </div>
  </section>

  <section class="card card--back" aria-label="Business card back">
    <div class="back__brand">
      <span class="back__dot" aria-hidden="true"></span>
      <span class="back__name">Velk Partners Building</span>
    </div>
    <div class="back__web">www.velkpartners.example</div>
  </section>
</body>
</html>
```